Website for a Psychologist in Private Practice

I need a cool web design for my website: www.drkalvoric.com. I would like it to look professional. Keep all the current content and add: Space for video; radio spots (see Silver Cedar Tunes Logo below for those); Quick Inquiry; Friendora link; 5 star rating on Rivo; a map; reviews from former patients. I am open to suggestions.

Target Market(s)

Those seeking individual and marital counseling.

Industry/Entity Type

Mental Health

Number of Pages Required

1 page

Font styles to use
Sans Serif
Other font styles liked:
• I'm open but no hard to read script

Requirements
Must have
• All the content on my home page with link for video and radio spots. List services and degrees and expertices (pics not necessary).
Nice to have
• A video of me and radio conversations (logo of Silver Cedar Tunes radio attached).
Should not have
• Cartoons, comedy, etc.... I don't need pictures of services (marital, depression, etc...) Just list those.

```html
<!DOCTYPE html>
<html lang="en">
<head>
<meta charset="utf-8">
<title>Dr. Marla J. Kalvoric – Clinical Psychologist</title>
<link rel="stylesheet" href="https://fonts.googleapis.com/css2?family=Josefin+Sans:wght@300;400;600;700&family=Roboto:wght@400;500;700&display=swap">
<style>
:root{
  --gold:#c8aa52;
  --gold-dark:#b8983f;
  --blue:#1f5d8c;
  --blue-deep:#1a5482;
  --blue-btn:#4a8ed0;
  --blue-label:#3a8ccb;
  --sand:#d9cbb4;
  --white:#ffffff;
  --ink:#4a4a4a;
  --field:#e8e8e8;
}
*{box-sizing:border-box;margin:0;padding:0}
html,body{width:1200px;height:2853px;overflow:hidden}
body{position:relative;background:var(--sand);font-family:"Roboto",sans-serif;color:var(--ink)}
.abs{position:absolute}

/* top info bar */
.info-bar{left:0;top:0;width:1200px;height:53px;background:var(--white);display:flex;align-items:center;padding-left:72px;gap:40px;font-size:14px;color:#666}
.info-bar span{display:flex;align-items:center;gap:9px}
.info-bar svg{width:14px;height:14px;fill:none;stroke:#888;stroke-width:2}

/* header */
.site-header{left:0;top:53px;width:1200px;height:80px;background:var(--gold);display:flex;align-items:center;justify-content:space-between;padding:0 72px;border-bottom:3px solid var(--gold-dark)}
.brand{font-family:"Josefin Sans",sans-serif;font-size:36px;color:var(--white);font-weight:400}
.brand b{font-weight:700}
.main-nav{display:flex;gap:24px;font-size:16px;font-weight:700;color:var(--white);letter-spacing:.3px}

/* beach band */
.beach{left:0;top:133px;width:1200px;height:960px;background:linear-gradient(180deg,#5fb3c6 0%,#88c9d4 45%,#e9e4d8 68%,var(--sand) 80%)}
.hero-frame{left:72px;top:162px;width:1056px;height:532px;background:rgba(255,255,255,.55)}
.hero-photo{left:91px;top:181px;width:1018px;height:494px;background:linear-gradient(90deg,#3b4a22 0%,#c99a3a 25%,#6b6a36 45%,#c7b08e 70%,#2f6a9a 100%)}
.hero-title{left:152px;top:378px;width:380px;font-family:"Josefin Sans",sans-serif;font-weight:600;font-size:32px;line-height:35px;color:var(--white)}
.hero-arrow{top:412px;width:34px;height:34px}
.hero-arrow circle{fill:rgba(255,255,255,.3);stroke:#fff;stroke-width:2}
.hero-arrow path{fill:none;stroke:#fff;stroke-width:3}

/* feature circles */
.feature{top:732px;width:324px;height:324px;border-radius:50%;overflow:hidden;border:6px solid #eae2d3;box-shadow:0 2px 6px rgba(0,0,0,.2)}
.feature .pic{position:absolute;inset:0}
.feature .label{position:absolute;left:0;bottom:0;width:100%;height:74px;background:var(--blue-label);color:#fff;font-family:"Josefin Sans",sans-serif;font-weight:600;font-size:23px;text-align:center;padding-top:14px}
.play{position:absolute;left:119px;top:90px;width:74px;height:74px}
.station-name{position:absolute;left:0;top:176px;width:100%;text-align:center;font-family:"Josefin Sans",sans-serif;font-weight:600;font-size:23px;color:#fff}

/* welcome */
.welcome-band{left:0;top:1084px;width:1200px;height:668px;background:var(--blue);clip-path:polygon(0 0,100% 90px,100% 560px,0 100%)}
.welcome{left:76px;top:1150px;width:680px;color:#fff}
.welcome h1{font-family:"Josefin Sans",sans-serif;font-weight:400;font-size:29px;line-height:32px;margin-bottom:14px}
.welcome h1 b{font-weight:700}
.welcome p{font-size:13.6px;line-height:24px;margin-bottom:14px}

.inquiry{left:793px;top:1194px;width:333px;height:446px;background:#fff;border-radius:4px;overflow:hidden;box-shadow:0 3px 10px rgba(0,0,0,.25)}
.inquiry-head{background:var(--gold);height:148px;text-align:center;color:#fff;padding-top:14px}
.inquiry-head .kicker{font-weight:500;font-size:16px}
.inquiry-head .pill{display:inline-block;margin:8px 0 6px;width:300px;height:38px;border-radius:20px;background:var(--blue-btn);font-size:27px;line-height:39px}
.inquiry-head .note{font-size:13px;line-height:18px}
.inquiry form{padding:14px 18px}
.field{height:38px;background:var(--field);border-radius:4px;margin-bottom:11px;font-size:13px;color:#666;padding:11px 10px}
.field.tall{height:76px}
.submit{height:40px;background:#7aaee0;border:2px solid var(--blue-btn);border-radius:4px;color:#fff;font-weight:700;font-size:15px;text-align:center;line-height:36px;margin-top:16px}

/* reviews */
.reviews-title{left:0;top:1800px;width:1200px;text-align:center;font-family:"Josefin Sans",sans-serif;font-weight:300;font-size:30px;color:#fff}
.reviews-title::after{content:"";display:block;width:100px;height:2px;background:#fff;margin:10px auto 0}
.review{top:1902px;width:340px;text-align:center;color:#fff}
.review .avatar{width:76px;height:76px;border-radius:50%;margin:0 auto 32px;background:radial-gradient(circle,#b99378 0%,#6e5444 60%,#eee 62%);border:3px solid #eee}
.review p{font-size:13px;line-height:19px}
.review .name{font-family:"Josefin Sans",sans-serif;font-size:19px;margin-top:26px}
.review .role{font-size:12px}
.review-rule{top:1890px;width:1px;height:290px;background:rgba(255,255,255,.45)}

/* expertise */
.expertise{left:72px;top:2294px;width:1056px;height:160px;background:#fff}
.expertise .left{position:absolute;left:0;top:18px;width:528px;text-align:center;color:#777;font-size:15px;line-height:28px}
.expertise h3{font-family:"Josefin Sans",sans-serif;font-weight:400;font-size:24px;color:var(--blue-label)}
.expertise h4{font-family:"Josefin Sans",sans-serif;font-weight:400;font-size:20px;color:#777}
.expertise .divider{position:absolute;left:528px;top:16px;width:1px;height:128px;background:#ccc}
.expertise .right{position:absolute;left:528px;top:20px;width:528px;text-align:center}
.expertise .right .lead{font-family:"Josefin Sans",sans-serif;font-size:21px;color:#444}
.partners{display:flex;justify-content:center;gap:40px;margin-top:24px;align-items:center}
.partner{display:flex;align-items:center;gap:10px;font-family:"Josefin Sans",sans-serif;font-weight:600;font-size:24px;color:var(--blue)}
.partner i{display:block;width:22px;height:22px;background:var(--blue)}
.partner.alt{color:#8e8a2e}
.partner.alt i{background:#8e8a2e;border-radius:50%}

/* footer */
.site-footer{left:0;top:2528px;width:1200px;height:268px;background:var(--blue-deep);color:#fff;border-top:3px solid #134670}
.col{position:absolute;top:34px;font-size:13px;line-height:24px}
.col h5{font-size:13.5px;font-weight:700;text-transform:uppercase;margin-bottom:2px}
.contact-line{display:flex;gap:16px;align-items:center;margin-bottom:18px}
.contact-line svg{width:22px;height:22px;fill:none;stroke:#fff;stroke-width:2}
.map{width:242px;height:156px;margin-top:14px;background:linear-gradient(135deg,#e9e6dc,#d8dfe6 60%,#f1e7c8)}
.legal-bar{left:0;top:2796px;width:1200px;height:57px;background:var(--gold);display:flex;align-items:center;justify-content:space-between;padding:0 76px;color:#fff;font-size:13px}
.social{display:flex;gap:30px}
.social span{display:flex;align-items:center;gap:8px}
.social i{display:block;width:14px;height:14px;border-radius:50%;background:#fff}
</style>
</head>
<body>

<div class="abs info-bar">
  <span><svg viewBox="0 0 24 24"><path d="M12 22s7-7 7-12a7 7 0 0 0-14 0c0 5 7 12 7 12z"/><circle cx="12" cy="10" r="2.5"/></svg>415 Harbor Lane #210, Bayview, CA. 90412</span>
  <span><svg viewBox="0 0 24 24"><path d="M5 3h4l2 5-3 2a12 12 0 0 0 6 6l2-3 5 2v4a2 2 0 0 1-2 2A17 17 0 0 1 3 5a2 2 0 0 1 2-2z"/></svg>Call Now: (555) 218 4093</span>
  <span><svg viewBox="0 0 24 24"><rect x="3" y="5" width="18" height="14"/><path d="M3 5l9 8 9-8"/></svg>Email: mk@drkalvoric.com</span>
</div>

<header class="abs site-header">
  <div class="brand">Dr. <b>Marla J. Kalvoric</b></div>
  <nav class="main-nav"><span>HOME</span><span>SESSIONS</span><span>RESOURCES</span><span>BIO</span><span>CONTACT</span></nav>
</header>

<div class="abs beach" role="img" aria-label="Ocean waves washing onto a sandy beach"></div>
<div class="abs hero-frame"></div>
<div class="abs hero-photo" role="img" aria-label="Sunlight through a forest beside a portrait of the psychologist"></div>
<div class="abs hero-title">Lorem ipsum dolor sit amet, consectetur adipiscing elit</div>
<svg class="abs hero-arrow" style="left:102px" viewBox="0 0 34 34"><circle cx="17" cy="17" r="15"/><path d="M20 10l-7 7 7 7"/></svg>
<svg class="abs hero-arrow" style="left:1063px" viewBox="0 0 34 34"><circle cx="17" cy="17" r="15"/><path d="M14 10l7 7-7 7"/></svg>

<div class="abs feature" style="left:66px">
  <div class="pic" role="img" aria-label="Portrait of the psychologist" style="background:linear-gradient(160deg,#7fb4d6,#e3c9a2 55%,#2f73a8)"></div>
  <div class="label">Dr. Marla K</div>
</div>
<div class="abs feature" style="left:437px">
  <div class="pic" role="img" aria-label="Video still of a counseling session" style="background:linear-gradient(160deg,#c9c3b8,#8a8f96 55%,#4e6c8c)"></div>
  <svg class="play" viewBox="0 0 74 74"><circle cx="37" cy="37" r="33" fill="rgba(0,0,0,.25)" stroke="#fff" stroke-width="5"/><path d="M29 22l22 15-22 15z" fill="#fff"/></svg>
  <div class="label">Watch Our Video</div>
</div>
<div class="abs feature" style="left:798px">
  <div class="pic" role="img" aria-label="Radio show artwork" style="background:linear-gradient(180deg,#7fc3c4,#5aa7b0)"></div>
  <div class="station-name">Silver Cedar Tunes</div>
  <div class="label">Radio Spots</div>
</div>

<div class="abs welcome-band"></div>
<section class="abs welcome">
  <h1>Welcome to<br>Dr. <b>Marla J. Kalvoric</b></h1>
  <p>I'm so glad you are here. Choosing to see a professional for issues in your life can be difficult but also possibly life changing. Many postpone seeking help because they believe doing so acknowledges failure on their part. Really? We seek the help of experts all the time (contractors, mechanics, chefs, etc...) and what is more important than your life? Consulting with a neutral party to act in your best interest can be time well spent. So if you are willing to take the time to invest in counseling, make sure that it is with someone that is worth your time.</p>
  <p>Choose a licensed psychologist with a doctoral degree (Ph.D. or PsyD.) - both have over 10 years of education in the field of psychology, extensive internships and comprehensive licensing exams. Others have far less education if any. Also, consider the therapist's approach to therapy. I use a straightforward approach (psychobabble available upon request) with brief, solution-oriented sessions.</p>
  <p>Experience also separates good psychologists from others with fewer and more proficient sessions. My 20+ years of professional experience and my life experience contributes to the empathetic perspective I use to relate to each person I see. I also believe it is the reason 90% of my practice is referral based and why many other psychologists in the area seek my services.</p>
  <p><b>DO NOT COMPROMISE.</b> Find an educated, licensed, experienced professional that you can relate to. Think about what it took to get you here and the importance resolving this issue can have on your life.</p>
</section>

<aside class="abs inquiry">
  <div class="inquiry-head">
    <div class="kicker">CONTACT US TODAY FOR YOUR</div>
    <div class="pill">QUICK INQUIRY</div>
    <div class="note">Fill out the form below and we'll be in touch<br>within 24 hours!</div>
  </div>
  <form>
    <div class="field">Name</div>
    <div class="field">Email</div>
    <div class="field">Phone</div>
    <div class="field tall">How Can we help you?</div>
    <div class="submit">SUBMIT</div>
  </form>
</aside>

<h2 class="abs reviews-title">Reviews From Patients</h2>
<div class="abs review-rule" style="left:421px"></div>
<div class="abs review-rule" style="left:781px"></div>
<article class="abs review" style="left:70px">
  <div class="avatar" role="img" aria-label="Patient portrait"></div>
  <p>Lorem ipsum dolor sit amet, consectetur adipiscing elit, sed do eiusmod tempor incididunt ut labore et dolore magna aliqua. Ut enim ad minim veniam, quis nostrud exercitation ullamco laboris nisi ut aliquip ex ea commodo consequat. Duis aute irure dolor in reprehenderit in voluptate velit esse cillum dolore eu fugiat nulla pariatur. Excepteur sint occaecat cupidatat non proident, sunt in culpa qui officia deserunt mollit anim id est laborum.</p>
  <div class="name">Evan Marsh</div><div class="role">Lorem ipsum dolor</div>
</article>
<article class="abs review" style="left:431px">
  <div class="avatar" role="img" aria-label="Patient portrait"></div>
  <p>Lorem ipsum dolor sit amet, consectetur adipiscing elit, sed do eiusmod tempor incididunt ut labore et dolore magna aliqua. Ut enim ad minim veniam, quis nostrud exercitation ullamco laboris nisi ut aliquip ex ea commodo consequat. Duis aute irure dolor in reprehenderit in voluptate velit esse cillum dolore eu fugiat nulla pariatur. Excepteur sint occaecat cupidatat non proident, sunt in culpa qui officia deserunt mollit anim id est laborum.</p>
  <div class="name">Evan Marsh</div><div class="role">Lorem ipsum dolor</div>
</article>
<article class="abs review" style="left:791px">
  <div class="avatar" role="img" aria-label="Patient portrait"></div>
  <p>Lorem ipsum dolor sit amet, consectetur adipiscing elit, sed do eiusmod tempor incididunt ut labore et dolore magna aliqua. Ut enim ad minim veniam, quis nostrud exercitation ullamco laboris nisi ut aliquip ex ea commodo consequat. Duis aute irure dolor in reprehenderit in voluptate velit esse cillum dolore eu fugiat nulla pariatur. Excepteur sint occaecat cupidatat non proident, sunt in culpa qui officia deserunt mollit anim id est laborum.</p>
  <div class="name">Evan Marsh</div><div class="role">Lorem ipsum dolor</div>
</article>

<section class="abs expertise">
  <div class="left">
    <h3>EXPERTISE</h3>
    <div>Dating &nbsp;•&nbsp; Marriage &nbsp;•&nbsp; Parenting &amp; Professional</div>
    <h4>RELATIONSHIPS</h4>
    <div>Depression &amp; Anxiety Issues &nbsp;•&nbsp; Personality Disorders &nbsp;•&nbsp; Life Management</div>
  </div>
  <div class="divider"></div>
  <div class="right">
    <div class="lead">A portion of all revenue is donated to</div>
    <div class="partners">
      <div class="partner"><i></i>Hopewell Kids</div>
      <div class="partner alt"><i></i>Brightpath Homes</div>
    </div>
  </div>
</section>

<footer class="abs site-footer">
  <div class="col" style="left:72px;width:280px">
    <h5>Clinical Psychologist</h5>
    <div style="margin-top:-6px">California # PSY20518</div>
    <div style="margin-top:8px">Doctoral Degree in Clinical Psychology<br>Masters Degree in Counseling<br>Psychology Doctoral Internship, Coastal<br>University Medical Center Masters Internship,<br>Linden Clinic</div>
  </div>
  <div class="col" style="left:344px;width:240px">
    <h5>Contact Information</h5>
    <div class="contact-line" style="margin-top:12px"><svg viewBox="0 0 24 24"><path d="M12 22s7-7 7-12a7 7 0 0 0-14 0c0 5 7 12 7 12z"/><circle cx="12" cy="10" r="2.5"/></svg><span style="line-height:18px">415 Harbor Lane, Suite 210<br>Bayview, CA 90412</span></div>
    <div class="contact-line" style="font-size:18px"><svg viewBox="0 0 24 24"><path d="M5 3h4l2 5-3 2a12 12 0 0 0 6 6l2-3 5 2v4a2 2 0 0 1-2 2A17 17 0 0 1 3 5a2 2 0 0 1 2-2z"/></svg>(555) 218 4093</div>
    <div class="contact-line"><svg viewBox="0 0 24 24"><rect x="3" y="5" width="18" height="14"/><path d="M3 5l9 8 9-8"/></svg>mk@drkalvoric.com</div>
  </div>
  <div class="col" style="left:614px">
    <h5>Find Us On Map</h5>
    <div class="map" role="img" aria-label="Street map showing the office location"></div>
  </div>
  <div class="col" style="left:884px">
    <h5>Quick Links</h5>
    <div>Home<br>Sessions<br>Resources<br>Bio<br>Contact</div>
  </div>
</footer>

<div class="abs legal-bar">
  <span>©2016 Dr. Marla J. Kalvoric. All Rights Reserved.</span>
  <div class="social"><span><i></i>Rivo</span><span><i></i>Friendora</span><span><i></i>Chirpline</span></div>
</div>

</body>
</html>
```